Web Design For Marlow Pool Service

We are working with a company that wants a website for their pool service. Some sites to use for content/competitors and inspiration:
https://sacramento.brightwaterpoolco.example/builder/newbuild/repair/ppc
https://hollowbrookpoolcareplus.example/
https://lakemontpoolservice.example/
https://www.dravenspoolresurfacing.example/pool-renovation-ga/
Thank you for taking the time to consider designing a website for us. We are web developers based in Stockton, CA, USA. Most of our projects go through the same process. Understanding this process may help you win a project with us. We custom-code all of our websites in-house. We don’t have any requirements as to what tools you use for your design, but we prefer Figma files. For any design that we label as four-stars, we send it to the client for review. The client picks the final design they want us to use. Once we complete this process, we will continue to show additional clients all the four-star sites and purchase them later. Your designs will have multiple chances to sell. For better chances of success, we ask that you follow these guidelines.
IMAGES:
If you use any images or icons in the design, we ask that you have a link to the asset so we can purchase the image/icon. Most of the designs we submit do not have the customer’s images on them unless they have some great images. Be creative; show us the feeling you are trying to portray with your image choices. Use any royalty-free site you choose. We subscribe to Adobe and mainly use their images, but we can purchase images outside of Adobe. PLEASE NOTE: we will not submit designs to clients with watermarks on the images.
FONTS:
We ask that you identify the fonts used in the design. This can be done in a message if you want. We typically use Google Fonts and Adobe Fonts.
CONTENT:
We're always open to different content and ideas. We often submit designs with stock images so the client can see our vision. We typically take pictures after the website launch to use their images with our vision. Lorem Ipsum is fine for paragraphs, but we ask that you write the headers in correct English. We want to be able to show the vision and identify the sections of the website.
INSPIRATION:
We typically add a couple of links in the brief of websites we like to help you get started in your design.
REVISIONS:
We do not often ask for revisions of the designs unless we see something in the design that may not appeal to the client. If there are slight changes that we want to make, we do that in the development process.
FEEDBACK:
We rarely give feedback on designs during the design process. We are working on many website projects and do not have the time to provide feedback. We usually respond if your request is well thought out and asks specific questions, but a note asking “feedback, please” usually goes unanswered.
Number of Pages Required
1 page
Look and feel
Each slider illustrates characteristics of the customer's brand and the style your logo design should communicate.

```html
<!DOCTYPE html>
<html lang="en">
<head>
<meta charset="utf-8">
<title>Marlow Pool Service</title>
<link rel="stylesheet" href="https://fonts.googleapis.com/css2?family=Marcellus&family=Roboto:wght@400;500;700&display=swap">
<style>
:root{
  --blue:#0b5cc0;
  --blue-dark:#0a449a;
  --blue-deep:#083a86;
  --blue-light:#1a78d6;
  --ink:#1d2433;
  --muted:#5d6575;
  --white:#ffffff;
  --pale:#eef4fc;
  --line:#d6e2f3;
}
*{box-sizing:border-box;margin:0;padding:0}
html,body{width:1200px;height:4392px;overflow:hidden}
body{font-family:"Roboto",sans-serif;color:var(--ink);background:var(--white);position:relative}
.abs{position:absolute}
.serif{font-family:"Marcellus",serif}
p{font-size:13px;line-height:1.65}
.btn{display:inline-block;font-size:11px;font-weight:700;letter-spacing:.5px;border-radius:20px;padding:10px 22px;text-transform:uppercase;white-space:nowrap}
.btn-solid{background:var(--blue);color:var(--white)}
.btn-outline{border:1.5px solid var(--blue);color:var(--blue);background:var(--white)}
.btn-ghost{border:1.5px solid var(--white);color:var(--white)}

.topbar{top:0;left:0;width:1200px;height:32px;background:var(--blue);color:var(--white);font-size:11px;display:flex;align-items:center;justify-content:space-between;padding:0 120px}
.topbar span{margin-right:22px}
.nav{top:32px;left:0;width:1200px;height:104px;background:var(--white);display:flex;align-items:center;padding:0 120px}
.brand{display:flex;align-items:center;gap:10px;font-family:"Marcellus",serif;font-size:24px;color:var(--blue);white-space:nowrap}
.brand i{width:16px;height:16px;border-radius:50%;background:var(--blue);display:block}
.menu{display:flex;gap:34px;margin-left:auto;margin-right:34px;font-size:13px;font-weight:500}
.menu a{color:var(--ink);text-decoration:none;padding-bottom:6px}
.menu a.active{color:var(--blue);border-bottom:2px solid var(--blue)}
.hero{top:136px;left:0;width:1200px;height:644px;background:linear-gradient(180deg,#5aa7e8 0%,#a6d0ef 38%,#6f9a5a 60%,#2f86c9 78%,#1f6fb8 100%)}
.hero-title{top:276px;left:150px;color:var(--white);font-size:42px;line-height:1.15;letter-spacing:1px}
.hero-text{top:384px;left:150px;width:300px;color:var(--white);font-size:12px}
.hero-btn{top:436px;left:150px}
.dot-arrow{width:34px;height:34px;border-radius:50%;background:var(--white);display:flex;align-items:center;justify-content:center}
.h-section{font-family:"Marcellus",serif;font-size:38px;color:var(--ink);letter-spacing:1px}
.about-photo{top:820px;left:190px;width:380px;height:380px;border-radius:50%;border:12px solid var(--blue);background:linear-gradient(160deg,#d9d3c4,#8fb7d8 55%,#2c79bf)}
.about-ring{top:800px;left:170px;width:420px;height:420px;border-radius:50%;border:2px solid var(--line)}
.about-title{top:824px;left:620px}
.about-rule{top:880px;left:620px;width:60px;height:3px;background:var(--blue)}
.about-copy{top:900px;left:620px;width:460px;color:var(--muted)}
.about-copy p+p{margin-top:12px}
.about-btn{top:1200px;left:620px}
.svc-title{font-size:34px;color:var(--white);line-height:1.15;letter-spacing:1px}
.svc-copy{color:var(--white);opacity:.95}
.why-title{top:1900px;left:0;width:1200px;text-align:center}
.feat{display:flex;align-items:center;gap:16px;font-size:13px;font-weight:700;color:var(--ink)}
.feat .ic{width:54px;height:54px;border-radius:50%;background:var(--pale);display:flex;align-items:center;justify-content:center;flex:none}
.feat-l{text-align:right}
.card{top:2690px;width:292px;height:276px;background:rgba(255,255,255,.14);border:1px solid rgba(255,255,255,.35);border-radius:6px;padding:48px 22px 0;text-align:center;color:var(--white)}
.card p{font-size:12px}
.card h4{font-size:17px;margin-top:14px;font-weight:700}
.card small{font-size:11px;opacity:.85}
.quote{top:-28px;left:118px;width:56px;height:56px;border-radius:50%;background:var(--white);display:flex;align-items:center;justify-content:center}
.g{border-radius:2px}
.foot-h{font-size:18px;font-weight:700;color:var(--white)}
.foot-list{list-style:none;color:var(--white);font-size:12px}
.foot-list li{display:flex;align-items:flex-start;gap:10px;margin-bottom:12px;line-height:1.4}
.foot-list svg{flex:none;margin-top:2px}
</style>
</head>
<body>

<div class="abs topbar">
  <div><span>&#9719; Monday - Saturday : 8AM - 5.30PM</span><span>Sunday : Closed</span></div>
  <div><span>&#9742; Phone : +1 555 014 2286</span><span style="margin-right:0">&#9993; Email : info@marlowpool.example</span></div>
</div>

<header class="abs nav">
  <div class="brand"><i></i>Marlow Pool Service</div>
  <nav class="menu">
    <a class="active">Home</a><a>About</a><a>Services</a><a>Gallery</a><a>Blog</a><a>Contact</a>
  </nav>
  <span class="btn btn-outline">&#9906; Find Our Pool</span>
</header>

<section class="abs hero" role="img" aria-label="Photo of a resort pool surrounded by palm trees and a villa under blue sky"></section>
<svg class="abs" style="top:676px;left:0" width="1200" height="110" viewBox="0 0 1200 110">
  <path d="M0 0 Q600 150 1200 0 L1200 110 L0 110 Z" fill="#fff"/>
</svg>
<h1 class="abs serif hero-title">BRING YOUR DREAM<br>POOL TO LIFE</h1>
<p class="abs hero-text">Lorem ipsum dolor sit amet, consectetur adipiscing elit, sed do eiusmod tempor incididunt ut labore et dolore magna aliqua.</p>
<span class="abs btn btn-solid hero-btn">Get Started</span>
<div class="abs dot-arrow" style="top:612px;left:558px"><svg width="10" height="10" viewBox="0 0 10 10"><path d="M7 1 3 5l4 4" stroke="#0b5cc0" stroke-width="2" fill="none"/></svg></div>
<div class="abs dot-arrow" style="top:612px;left:608px"><svg width="10" height="10" viewBox="0 0 10 10"><path d="M3 1l4 4-4 4" stroke="#0b5cc0" stroke-width="2" fill="none"/></svg></div>

<div class="abs about-ring"></div>
<div class="abs about-photo" role="img" aria-label="Photo of a technician cleaning a pool with a long brush"></div>
<h2 class="abs h-section about-title">ABOUT US</h2>
<div class="abs about-rule"></div>
<div class="abs about-copy">
  <p>Lorem ipsum dolor sit amet, consectetur adipiscing elit, sed do eiusmod tempor incididunt ut labore et dolore magna aliqua. Ut enim ad minim veniam, quis nostrud exercitation ullamco laboris nisi ut aliquip ex ea commodo consequat. Duis aute irure dolor in reprehenderit in voluptate velit esse cillum dolore eu fugiat nulla pariatur. Excepteur sint occaecat cupidatat non proident, sunt in culpa qui officia deserunt mollit anim id est laborum. Sed ut perspiciatis unde omnis iste natus error sit voluptatem accusantium.</p>
  <p>Ut enim ad minim veniam, quis nostrud exercitation ullamco laboris nisi ut aliquip ex ea commodo consequat. Duis aute irure dolor in reprehenderit in voluptate velit esse cillum dolore eu fugiat nulla pariatur. Excepteur sint occaecat cupidatat non proident.</p>
</div>
<span class="abs btn btn-outline about-btn">Learn More &#10140;</span>

<svg class="abs" style="top:1262px;left:0" width="1200" height="640" viewBox="0 0 1200 640">
  <polygon points="0,40 600,0 600,600 0,640" fill="#0a4fae"/>
  <polygon points="600,0 1200,48 1200,640 600,600" fill="#1470cf"/>
</svg>
<h3 class="abs serif svc-title" style="top:1390px;left:150px">POOL CLEANING<br>SERVICE</h3>
<p class="abs svc-copy" style="top:1490px;left:150px;width:400px">Lorem ipsum dolor sit amet, consectetur adipiscing elit, sed do eiusmod tempor incididunt ut labore et dolore magna aliqua. Ut enim ad minim veniam, quis nostrud exercitation ullamco laboris nisi ut aliquip ex ea commodo consequat. Duis aute irure dolor in reprehenderit in voluptate velit esse cillum dolore eu fugiat nulla pariatur. Excepteur sint occaecat cupidatat non proident, sunt in culpa qui officia deserunt mollit anim id est laborum.</p>
<span class="abs btn btn-ghost" style="top:1706px;left:150px">Learn More &#10140;</span>
<h3 class="abs serif svc-title" style="top:1390px;left:676px">SWIMMING POOL<br>REPAIR</h3>
<p class="abs svc-copy" style="top:1490px;left:676px;width:400px">Lorem ipsum dolor sit amet, consectetur adipiscing elit, sed do eiusmod tempor incididunt ut labore et dolore magna aliqua. Ut enim ad minim veniam, quis nostrud exercitation ullamco laboris nisi ut aliquip ex ea commodo consequat. Duis aute irure dolor in reprehenderit in voluptate velit esse cillum dolore eu fugiat nulla pariatur. Excepteur sint occaecat cupidatat non proident, sunt in culpa qui officia deserunt mollit anim id est laborum.</p>
<span class="abs btn btn-ghost" style="top:1706px;left:676px">Learn More &#10140;</span>

<h2 class="abs h-section why-title">WHY CHOOSE US</h2>
<svg class="abs" style="top:2040px;left:380px" width="440" height="440" viewBox="0 0 440 440">
  <circle cx="220" cy="220" r="205" fill="none" stroke="#0b5cc0" stroke-width="1.5"/>
  <circle cx="220" cy="220" r="180" fill="#0b5cc0"/>
  <g fill="#0b5cc0"><circle cx="30" cy="140" r="5"/><circle cx="16" cy="220" r="5"/><circle cx="30" cy="300" r="5"/><circle cx="410" cy="140" r="5"/><circle cx="424" cy="220" r="5"/><circle cx="410" cy="300" r="5"/></g>
</svg>
<div class="abs" style="top:2070px;left:430px;width:340px;height:340px;border-radius:50%;background:linear-gradient(180deg,#7fbbe8 0%,#b9dcf3 40%,#4b8f4f 55%,#2a9ad8 70%,#0e6fc0 100%)" role="img" aria-label="Photo of a backyard pool with lounge chairs"></div>

<div class="abs feat feat-l" style="top:2030px;left:130px;width:240px;justify-content:flex-end"><span>Experienced &amp;<br>Professional</span><span class="ic"><svg width="24" height="24" viewBox="0 0 24 24" fill="none" stroke="#0b5cc0" stroke-width="1.8"><circle cx="12" cy="9" r="6"/><path d="M8 14l-2 8 6-3 6 3-2-8"/></svg></span></div>
<div class="abs feat feat-l" style="top:2184px;left:110px;width:240px;justify-content:flex-end"><span>Competitive<br>Price</span><span class="ic"><svg width="24" height="24" viewBox="0 0 24 24" fill="none" stroke="#0b5cc0" stroke-width="1.8"><path d="M3 12l9-9h8v8l-9 9z"/><circle cx="16" cy="8" r="1.5"/></svg></span></div>
<div class="abs feat feat-l" style="top:2336px;left:130px;width:240px;justify-content:flex-end"><span>Large<br>Showroom</span><span class="ic"><svg width="24" height="24" viewBox="0 0 24 24" fill="none" stroke="#0b5cc0" stroke-width="1.8"><path d="M3 10l9-6 9 6v10H3z"/><path d="M9 20v-6h6v6"/></svg></span></div>

<div class="abs feat" style="top:2030px;left:830px;width:260px"><span class="ic"><svg width="24" height="24" viewBox="0 0 24 24" fill="none" stroke="#0b5cc0" stroke-width="1.8"><rect x="4" y="3" width="16" height="18" rx="2"/><path d="M8 12l3 3 5-6"/></svg></span><span>Licensed and<br>Insured</span></div>
<div class="abs feat" style="top:2184px;left:850px;width:260px"><span class="ic"><svg width="24" height="24" viewBox="0 0 24 24" fill="none" stroke="#0b5cc0" stroke-width="1.8"><circle cx="12" cy="12" r="9"/><path d="M12 7v5l3 3"/></svg></span><span>Free Estimates</span></div>
<div class="abs feat" style="top:2336px;left:830px;width:260px"><span class="ic"><svg width="24" height="24" viewBox="0 0 24 24" fill="none" stroke="#0b5cc0" stroke-width="1.8"><path d="M12 3l2.7 5.6 6.1.9-4.4 4.3 1 6.1L12 17l-5.4 2.9 1-6.1-4.4-4.3 6.1-.9z"/></svg></span><span>Readers Choice<br>Best of Riverton</span></div>

<svg class="abs" style="top:2500px;left:0" width="1200" height="650" viewBox="0 0 1200 650" role="img" aria-label="Rippling blue pool water background">
  <defs><linearGradient id="water" x1="0" y1="0" x2="1" y2="1"><stop offset="0" stop-color="#0d5fc6"/><stop offset=".5" stop-color="#0a4aa8"/><stop offset="1" stop-color="#0b57ba"/></linearGradient></defs>
  <polygon points="0,30 1200,0 1200,620 0,650" fill="url(#water)"/>
</svg>
<h2 class="abs h-section" style="top:2600px;left:0;width:1200px;text-align:center;color:#fff">TESTIMONIALS</h2>
<div class="abs" style="top:2816px;left:58px;color:#fff;font-size:26px">&#8249;</div>
<div class="abs" style="top:2816px;left:1128px;color:#fff;font-size:26px">&#8250;</div>

<div class="abs card" style="left:150px">
  <div class="abs quote"><svg width="22" height="18" viewBox="0 0 22 18" fill="#0b5cc0"><path d="M0 18V10Q0 2 8 0v4Q4 5 4 9h4v9zM12 18V10q0-8 8-10v4q-4 1-4 5h4v9z"/></svg></div>
  <p>Lorem ipsum dolor sit amet, consectetur adipiscing elit, sed do eiusmod tempor incididunt ut labore et dolore magna aliqua. Ut enim ad minim veniam, quis nostrud exercitation ullamco laboris nisi ut aliquip ex ea commodo consequat.</p>
  <h4>John Doe</h4><small>Company name</small>
</div>
<div class="abs card" style="left:454px">
  <div class="abs quote"><svg width="22" height="18" viewBox="0 0 22 18" fill="#0b5cc0"><path d="M0 18V10Q0 2 8 0v4Q4 5 4 9h4v9zM12 18V10q0-8 8-10v4q-4 1-4 5h4v9z"/></svg></div>
  <p>Lorem ipsum dolor sit amet, consectetur adipiscing elit, sed do eiusmod tempor incididunt ut labore et dolore magna aliqua. Ut enim ad minim veniam, quis nostrud exercitation ullamco laboris nisi ut aliquip ex ea commodo consequat.</p>
  <h4>John Doe</h4><small>Company name</small>
</div>
<div class="abs card" style="left:758px">
  <div class="abs quote"><svg width="22" height="18" viewBox="0 0 22 18" fill="#0b5cc0"><path d="M0 18V10Q0 2 8 0v4Q4 5 4 9h4v9zM12 18V10q0-8 8-10v4q-4 1-4 5h4v9z"/></svg></div>
  <p>Lorem ipsum dolor sit amet, consectetur adipiscing elit, sed do eiusmod tempor incididunt ut labore et dolore magna aliqua. Ut enim ad minim veniam, quis nostrud exercitation ullamco laboris nisi ut aliquip ex ea commodo consequat.</p>
  <h4>John Doe</h4><small>Company name</small>
</div>

<h2 class="abs h-section" style="top:3180px;left:0;width:1200px;text-align:center">GALLERY</h2>
<div class="abs g" style="top:3262px;left:150px;width:290px;height:210px;background:linear-gradient(160deg,#9fd2ee,#2b8fd0)" role="img" aria-label="Photo of a hand testing pool water"></div>
<div class="abs g" style="top:3490px;left:150px;width:290px;height:280px;background:linear-gradient(170deg,#7a5c8e,#3fa0d8 60%,#1c76c4)" role="img" aria-label="Photo of a pool at dusk"></div>
<div class="abs g" style="top:3262px;left:460px;width:290px;height:180px;background:linear-gradient(180deg,#e0e6ea,#3b9ad6 60%,#0f6bb8)" role="img" aria-label="Photo of a pool technician standing by a pool"></div>
<div class="abs g" style="top:3460px;left:460px;width:290px;height:310px;background:linear-gradient(180deg,#cfd8de,#5ab2e2 55%,#2183c9)" role="img" aria-label="Photo of an automatic pool cleaner in the water"></div>
<div class="abs g" style="top:3262px;left:770px;width:290px;height:200px;background:linear-gradient(180deg,#7fb4e0,#c7a874 45%,#2b8ed1)" role="img" aria-label="Photo of a pool with lounge chairs and umbrella"></div>
<div class="abs g" style="top:3480px;left:770px;width:290px;height:290px;background:linear-gradient(180deg,#5d9fd8,#9ac7e3 45%,#1f7cc6)" role="img" aria-label="Photo of a modern house with infinity pool"></div>

<svg class="abs" style="top:3860px;left:0" width="1200" height="532" viewBox="0 0 1200 532">
  <path d="M0 40 Q600 -40 1200 40 L1200 532 L0 532 Z" fill="#0a4aa8"/>
</svg>
<div class="abs brand" style="top:3970px;left:0;width:1200px;justify-content:center;color:#fff"><i style="background:#fff"></i>Marlow Pool Service</div>
<div class="abs" style="top:4072px;left:152px;width:448px;height:170px;background:linear-gradient(135deg,#e8eef0,#cfdccf 60%,#b7cde0)" role="img" aria-label="Map showing the service location"></div>
<div class="abs foot-h" style="top:4072px;left:660px">Contact Us</div>
<ul class="abs foot-list" style="top:4112px;left:660px;width:230px">
  <li><svg width="14" height="14" viewBox="0 0 24 24" fill="#fff"><path d="M12 2a7 7 0 0 0-7 7c0 5 7 13 7 13s7-8 7-13a7 7 0 0 0-7-7zm0 9.5A2.5 2.5 0 1 1 12 6.5a2.5 2.5 0 0 1 0 5z"/></svg><span>123, Lorem ipsum dolor sit amet,<br>street, Riverton</span></li>
  <li><svg width="14" height="14" viewBox="0 0 24 24" fill="#fff"><path d="M6.6 10.8a15 15 0 0 0 6.6 6.6l2.2-2.2a1 1 0 0 1 1-.25 11.4 11.4 0 0 0 3.6.6 1 1 0 0 1 1 1V20a1 1 0 0 1-1 1A17 17 0 0 1 3 4a1 1 0 0 1 1-1h3.5a1 1 0 0 1 1 1c0 1.25.2 2.45.6 3.6a1 1 0 0 1-.25 1z"/></svg><span>+1 555 014 2286</span></li>
  <li><svg width="14" height="14" viewBox="0 0 24 24" fill="#fff"><path d="M2 5h20v14H2zm2 2v.5l8 5 8-5V7z"/></svg><span>info@marlowpool.example</span></li>
</ul>
<div class="abs foot-h" style="top:4072px;left:948px">Quick Links</div>
<ul class="abs foot-list" style="top:4112px;left:948px">
  <li>&#8250; Home</li><li>&#8250; About</li><li>&#8250; Services</li><li>&#8250; Gallery</li><li>&#8250; Blog</li><li>&#8250; Contact</li>
</ul>
<div class="abs" style="top:4340px;left:150px;width:900px;height:1px;background:rgba(255,255,255,.3)"></div>
<div class="abs" style="top:4356px;left:0;width:1200px;text-align:center;color:#fff;font-size:11px">Copyright &copy; 2024 Company name - All Rights Reserved</div>

</body>
</html>
```